Boutique custom software development company needs new business card

Our nearly 20 year old custom software development company would like to better include the fact that we are now providing Bitcoin services. These new services are B2B include education (how to acquire and securely hold Bitcoin) and integrating Bitcoin payments into existing ecommerce sites or other existing systems. Please keep the card clean and simple. Attached is our current design and some other files. vextorial.com

Target Market(s)

businesses owners interested in long term relationship

Industry/Entity Type

Custom software development and Bitcoin

Contact Information for Business Card

Dale Parker, dale@vextorial.com, vextorial.com, (888) 555-VXTRL

Font styles to use
Other font styles liked:
• monospace

Requirements
Must have
• double-sided
Nice to have
• clean and simple
Should not have
• physical address

```html
<!DOCTYPE html>
<html lang="en">
<head>
<meta charset="utf-8">
<title>Vextorial Business Card</title>
<link rel="stylesheet" href="https://fonts.googleapis.com/css2?family=Roboto+Mono:wght@300;400;500;700&display=swap">
<style>
  :root {
    --navy: #131a45;
    --orange: #f07c24;
    --blue: #4173b8;
    --white: #ffffff;
    --page: #ffffff;
  }
  * { margin: 0; padding: 0; box-sizing: border-box; }
  html, body {
    width: 1200px;
    height: 1000px;
    overflow: hidden;
    background: var(--page);
    font-family: "Roboto Mono", monospace;
  }
  .canvas { position: relative; width: 1200px; height: 1000px; }

  .card { position: absolute; overflow: hidden; }
  .card--front { left: 265px; top: 93px; width: 668px; height: 382px; background: var(--navy); }
  .card--back  { left: 266px; top: 525px; width: 669px; height: 382px; background: var(--orange); }

  .card__shapes { position: absolute; inset: 0; }

  .brand-mark {
    position: absolute;
    left: 44px; top: 108px;
    display: flex; align-items: center; gap: 14px;
  }
  .brand-mark__square { width: 89px; height: 89px; background: var(--blue); }
  .brand-mark__name { color: var(--white); font-size: 21px; font-weight: 500; letter-spacing: 0.5px; }

  .contact__name {
    position: absolute; left: 45px; top: 239px;
    color: var(--orange); font-size: 25px; font-weight: 500; letter-spacing: 0.6px;
  }
  .contact__line {
    position: absolute; left: 46px;
    color: var(--white); font-size: 17px; font-weight: 500; letter-spacing: 0.2px;
  }
  .contact__line--email { top: 285px; }
  .contact__line--phone { top: 313px; }
  .contact__web {
    position: absolute; right: 49px; top: 313px;
    color: var(--white); font-size: 16.5px; font-weight: 400; letter-spacing: 0;
  }

  .wordmark {
    position: absolute; left: 0; right: 0; top: 132px;
    text-align: center;
    color: var(--white); font-size: 64px; font-weight: 700; letter-spacing: 0; line-height: 1;
  }
  .tagline {
    position: absolute; left: 0; right: 0; top: 216px;
    text-align: center;
    color: var(--white); font-size: 19.5px; font-weight: 400; letter-spacing: 0.4px;
  }
  .services {
    position: absolute; left: 0; right: 0; top: 250px;
    text-align: center;
    color: var(--navy); font-size: 16.5px; font-weight: 500; letter-spacing: 0.2px;
  }
</style>
</head>
<body>
<main class="canvas">
  <section class="card card--front" aria-label="Card front">
    <svg class="card__shapes" width="668" height="382" viewBox="0 0 668 382" aria-hidden="true">
      <polygon points="516,0 668,0 668,88 591,133" fill="var(--orange)"/>
      <polygon points="282,382 366,334 394,382" fill="var(--blue)"/>
    </svg>
    <div class="brand-mark">
      <div class="brand-mark__square"></div>
      <span class="brand-mark__name">VEXTORIAL</span>
    </div>
    <h1 class="contact__name">Dale Parker</h1>
    <p class="contact__line contact__line--email">M:dale@vextorial.com</p>
    <p class="contact__line contact__line--phone">T:(888) 555-VXTRL</p>
    <p class="contact__web">www.vextorial.com</p>
  </section>

  <section class="card card--back" aria-label="Card back">
    <p class="wordmark">VEXTORIAL</p>
    <p class="tagline">developer of custom applications</p>
    <p class="services">bitcoin education &amp; payment integration</p>
  </section>
</main>
</body>
</html>
```